Business Card Design Project

use presentation folder design and my logo and make 4 over 4 business cards

Industry/Entity Type

Business

Requirements
Must have
• use the design from my presentation folder and put my logo on it

Name
Title
phone
fax
email

```html
<!DOCTYPE html>
<html lang="en">
<head>
<meta charset="utf-8">
<title>NorthPath Counseling – Business Cards</title>
<link rel="stylesheet" href="https://fonts.googleapis.com/css2?family=PT+Sans:wght@400;700&display=swap">
<style>
  :root {
    --canvas: #e9e7e4;
    --card-white: #fbfbfa;
    --tile-grey: #e4e5e7;
    --tile-blue: #eef2f7;
    --tile-beige: #f3ebe2;
    --tile-white: #f6f6f6;
    --brown: #8b4a14;
    --copper: #b0661e;
    --ink: #5a5a5a;
    --back-dark: #431a04;
    --back-mid: #5e2709;
    --silver: #c9c9c9;
  }
  * { box-sizing: border-box; margin: 0; padding: 0; }
  html, body { width: 1200px; height: 1000px; overflow: hidden; }
  body {
    background: var(--canvas);
    font-family: "PT Sans", Arial, sans-serif;
    display: flex;
    flex-direction: column;
    align-items: center;
    justify-content: center;
    gap: 60px;
  }
  .card {
    width: 700px;
    height: 400px;
    border-radius: 14px;
    position: relative;
    overflow: hidden;
    box-shadow: 0 6px 18px rgba(0,0,0,.18);
  }

  /* Front */
  .card-front { background: var(--card-white); }
  .tile { position: absolute; border-radius: 14px; }
  .tile-grey  { left: 80px;  top: -14px; width: 230px; height: 175px; background: var(--tile-grey); }
  .tile-top   { left: 0;     top: -14px; width: 64px;  height: 40px;  background: var(--tile-beige); }
  .tile-blue  { left: 330px; top: -14px; width: 384px; height: 175px; background: var(--tile-blue); }
  .tile-logo  { left: -14px; top: 180px; width: 324px; height: 234px; background: var(--tile-white); }
  .tile-beige { left: 330px; top: 180px; width: 320px; height: 234px; background: var(--tile-beige); }
  .tile-edge  { left: 666px; top: 180px; width: 60px;  height: 234px; background: var(--tile-beige); opacity: .7; }

  .person { position: absolute; right: 40px; top: 36px; text-align: right; }
  .person-name { color: var(--brown); font-weight: 700; font-size: 28px; letter-spacing: .5px; }
  .person-title { color: #8a8a8a; font-size: 17px; }

  .brand { position: absolute; left: 30px; top: 228px; width: 260px; }
  .brand-row { display: flex; align-items: center; gap: 12px; }
  .brand-dot { width: 22px; height: 22px; border-radius: 50%; background: var(--copper); flex: none; }
  .brand-name { color: var(--copper); font-size: 34px; font-weight: 400; line-height: 1.05; }
  .brand-tag { color: #444; font-size: 17px; margin-top: 8px; letter-spacing: .3px; white-space: nowrap; }

  .contact { position: absolute; left: 352px; top: 202px; color: var(--ink); font-size: 16px; line-height: 1.45; }
  .contact-head { font-weight: 700; text-decoration: underline; letter-spacing: .5px; color: #555; }
  .contact-line { display: flex; align-items: center; gap: 7px; }
  .contact-line svg { width: 16px; height: 16px; flex: none; }
  .contact-web { color: var(--brown); font-weight: 700; margin-top: 6px; }

  /* Back */
  .card-back {
    background: radial-gradient(ellipse at 40% 45%, var(--back-mid) 0%, var(--back-dark) 85%);
  }
  .back-brand { position: absolute; left: 0; right: 0; top: 118px; text-align: center; }
  .back-brand .brand-row { justify-content: center; gap: 16px; }
  .back-brand .brand-dot { width: 28px; height: 28px; }
  .back-brand .brand-name { font-size: 56px; white-space: nowrap; }
  .back-rule { width: 480px; height: 1px; background: var(--silver); opacity: .7; margin: 16px auto 10px; }
  .back-tag { color: var(--silver); font-size: 22px; letter-spacing: .5px; }
  .back-web { color: #e5d8cc; font-size: 20px; margin-top: 44px; letter-spacing: .5px; }
</style>
</head>
<body>

<section class="card card-front" aria-label="Business card front">
  <div class="tile tile-top"></div>
  <div class="tile tile-grey"></div>
  <div class="tile tile-blue"></div>
  <div class="tile tile-logo"></div>
  <div class="tile tile-beige"></div>
  <div class="tile tile-edge"></div>

  <div class="person">
    <div class="person-name">Dorian Ellsworth</div>
    <div class="person-title">Founder / CEO</div>
  </div>

  <div class="brand">
    <div class="brand-row">
      <span class="brand-dot"></span>
      <span class="brand-name">NorthPath<br>Counseling</span>
    </div>
    <div class="brand-tag">a pro active addiction center</div>
  </div>

  <div class="contact">
    <div class="contact-head">CORPORATE OFFICE</div>
    <div>4870 Alder Creek Dr. N.W. Suite 210</div>
    <div>Marietta GA 30060</div>
    <div class="contact-line">
      <svg viewBox="0 0 16 16"><circle cx="8" cy="8" r="7.5" fill="#8b4a14"/><path d="M5.5 4.5l1.6 1.8-.8 1c.5 1 1.2 1.7 2.2 2.2l1-.8 1.8 1.6-.9 1.2C8.3 11.3 5.2 8.2 4.5 5.4z" fill="#fff"/></svg>
      404.555.0182
    </div>
    <div class="contact-line">
      <svg viewBox="0 0 16 16"><circle cx="8" cy="8" r="7.5" fill="#8b4a14"/><rect x="4.5" y="6" width="7" height="5" rx="1" fill="#fff"/><rect x="6" y="4" width="4" height="2.5" fill="#fff"/></svg>
      678.555.0147
    </div>
    <div class="contact-line">
      <svg viewBox="0 0 16 16"><circle cx="8" cy="8" r="7.5" fill="#8b4a14"/><rect x="4" y="5.2" width="8" height="5.6" fill="#fff"/><path d="M4 5.2l4 3 4-3" fill="none" stroke="#8b4a14" stroke-width=".9"/></svg>
      NorthPathCounseling@mail.com
    </div>
    <div class="contact-web">www.northpathcare.com</div>
  </div>
</section>

<section class="card card-back" aria-label="Business card back">
  <div class="back-brand">
    <div class="brand-row">
      <span class="brand-dot"></span>
      <span class="brand-name">NorthPath Counseling</span>
    </div>
    <div class="back-rule"></div>
    <div class="back-tag">a pro active addiction center</div>
    <div class="back-web">www.northpathcare.com</div>
  </div>
</section>

</body>
</html>
```